Powerpoint and Word template required

We need PowerPoint and Word templates for all of our company branded materials and stationary. We have recently rebranded our website and would like something that is reflective of our new corporate branding. A sample of some of the documents we have created recently are attached and our website is below

http://lorwynmedical.com.au/

The word template will be used for all letters we send to clients and customers and we think we want the logo and ISO 9001 cert to only appear on the first page.

The powerpoint template has to be flexible as we use this for both marketing and training purposes. I have attached a couple of samples of the types of documents we create and note that these are very basic / crude and we would be looking for something that is a significant improvement on these

In the powerpoint template it would be good to have lots of standard layouts within the template, e.g. different 'standard layouts for multiple elements on a page including pictures and text etc.
Updates

Project Deadline Extended
Reason: Still looking for a professional yet modern template and important to us that we can see more tan just a title slide and the layout of the other slide master slides is very important to us. Many thanks, Dale

Industry/Entity Type

Healthcare

Font styles to use
Sans Serif

Colors
33a6d7

Requirements
Must have
• Templates must be versatile for use; powerpoint template must be able to be used for training materials and weel as marketing / pitch books.
• Word template must be able to be used as a basis for our corporate letter head through to RFP response type documents as well as Reference / Operating manual type of documents
• In terms of the design it must be consistent with our new corporate image which is best represented by our new website design; www.lorwynmedical.com

```html
<!DOCTYPE html>
<html lang="en">
<head>
<meta charset="utf-8">
<title>Constant Low Pressure – Lorwyn Medical</title>
<link href="https://fonts.googleapis.com/css2?family=Roboto+Condensed:wght@400;700&display=swap" rel="stylesheet">
<style>
  :root {
    --brand-blue: #2a7fc4;
    --title-blue: #2b7cc0;
    --rule-grey: #c9d3dc;
    --page-bg: #eef2f6;
    --band-bg: #f4f7fa;
    --white: #ffffff;
    --footer-text: #2d4a66;
    --badge-dark: #222222;
    --photo-tone-a: #8d8590;
    --photo-tone-b: #a19ca1;
  }
  * { margin: 0; padding: 0; box-sizing: border-box; }
  html, body { width: 1200px; height: 900px; overflow: hidden; }
  body {
    font-family: "Roboto Condensed", "Arial Narrow", sans-serif;
    background: var(--page-bg);
    position: relative;
  }
  .slide { position: absolute; inset: 0; background: var(--page-bg); }

  .header {
    position: absolute; left: 0; top: 0; width: 1200px; height: 117px;
    background: var(--band-bg);
  }
  .slide-title {
    position: absolute; left: 17px; top: 20px;
    font-size: 35px; font-weight: 700; color: var(--title-blue);
    letter-spacing: 0.2px; line-height: 1.2;
  }
  .title-rule {
    position: absolute; left: 15px; top: 66px; width: 393px; height: 3px;
    background: var(--rule-grey);
  }
  .brand {
    position: absolute; right: 27px; top: 28px;
    display: flex; align-items: center; gap: 12px;
  }
  .brand-mark {
    width: 48px; height: 48px; border-radius: 6px; background: var(--brand-blue);
  }
  .brand-name {
    font-size: 46px; font-weight: 700; color: var(--brand-blue); line-height: 1;
  }

  .feature-panel {
    position: absolute; left: 0; top: 117px; width: 537px; height: 674px;
    background: var(--brand-blue);
  }
  .feature-list { list-style: none; position: absolute; left: 30px; top: 81px; }
  .feature-item {
    display: flex; align-items: flex-start; gap: 14px;
    color: var(--white); font-size: 29px; font-weight: 700;
    line-height: 45px; margin-bottom: 42px; max-width: 470px;
  }
  .feature-icon { flex: none; width: 48px; height: 46px; }

  .product-photo {
    position: absolute; left: 537px; top: 117px; width: 663px; height: 674px;
    background: linear-gradient(180deg, var(--photo-tone-a) 0%, var(--photo-tone-b) 100%);
  }

  .footer {
    position: absolute; left: 0; top: 791px; width: 1200px; height: 109px;
    background: var(--band-bg);
  }
  .copyright {
    position: absolute; left: 0; top: 838px; width: 197px; height: 47px;
    background: var(--brand-blue); color: var(--white);
    font-size: 20px; display: flex; align-items: center; padding-left: 15px;
  }
  .site-url {
    position: absolute; left: 440px; top: 847px; width: 370px; text-align: center;
    font-size: 22px; color: var(--footer-text);
  }
  .page-number {
    position: absolute; left: 1146px; top: 848px; width: 42px; height: 42px;
    background: var(--badge-dark); color: var(--white); border-radius: 4px;
    font-size: 20px; display: flex; align-items: center; justify-content: center;
  }
</style>
</head>
<body>
<div class="slide">
  <header class="header">
    <h1 class="slide-title">CONSTANT LOW PRESSURE</h1>
    <div class="title-rule"></div>
    <div class="brand">
      <span class="brand-mark"></span>
      <span class="brand-name">Lorwyn</span>
    </div>
  </header>

  <section class="feature-panel">
    <ul class="feature-list">
      <li class="feature-item">
        <svg class="feature-icon" viewBox="0 0 48 46"><rect x="2" y="2" width="44" height="42" rx="7" fill="none" stroke="#fff" stroke-width="3"/><path d="M14 23 l7 7 l13 -14" fill="none" stroke="#fff" stroke-width="3.5" stroke-linecap="round" stroke-linejoin="round"/></svg>
        <span>HIGH SPECIFICATION FOAMS</span>
      </li>
      <li class="feature-item">
        <svg class="feature-icon" viewBox="0 0 48 46"><rect x="2" y="2" width="44" height="42" rx="7" fill="none" stroke="#fff" stroke-width="3"/><path d="M14 23 l7 7 l13 -14" fill="none" stroke="#fff" stroke-width="3.5" stroke-linecap="round" stroke-linejoin="round"/></svg>
        <span>STRETCH COVER</span>
      </li>
      <li class="feature-item">
        <svg class="feature-icon" viewBox="0 0 48 46"><rect x="2" y="2" width="44" height="42" rx="7" fill="none" stroke="#fff" stroke-width="3"/><path d="M14 23 l7 7 l13 -14" fill="none" stroke="#fff" stroke-width="3.5" stroke-linecap="round" stroke-linejoin="round"/></svg>
        <span>MULTI LAYERS OF DIFFERENT<br>DENSITY FOAMS</span>
      </li>
    </ul>
  </section>

  <div class="product-photo" role="img" aria-label="Photo of a pressure-care mattress with its stretch cover folded back, showing layered foams of different densities"></div>

  <footer class="footer"></footer>
  <div class="copyright">Copyright text here</div>
  <div class="site-url">||&nbsp;&nbsp; www.lorwynmedical.com.au &nbsp;&nbsp;||</div>
  <div class="page-number">01</div>
</div>
</body>
</html>
```